Harborline Benches business cards

I’d like a business card design that includes my logo, a tag line and my contact info. Black, textured background. My contact info color should match the orange and blue gradients. Tagline under logo: “Wooden Tables and Furniture of the Highest Quality”

Target Market(s)

High end furniture buyers

Contact Information for Business Card

Contact info, logo and tagline

```html
<!DOCTYPE html>
<html lang="en">
<head>
<meta charset="utf-8">
<title>Harborline Benches – Business Cards</title>
<link rel="stylesheet" href="https://fonts.googleapis.com/css2?family=Bebas+Neue&family=Poppins:wght@400;500;600&display=swap">
<style>
  :root {
    --backdrop: #b6b6b6;
    --card: #ffffff;
    --orange: #ed7326;
    --blue: #0054aa;
    --ink: #1f1f1f;
    --tagline-ink: #333333;
    --rule: #8a8a8a;
  }
  * { box-sizing: border-box; margin: 0; padding: 0; }
  html, body { width: 1200px; height: 1200px; overflow: hidden; }
  body { background: var(--backdrop); position: relative; font-family: "Poppins", sans-serif; }

  .card {
    position: absolute;
    top: 303px;
    height: 594px;
    background: var(--card);
    box-shadow: 4px 4px 3px rgba(0,0,0,0.55);
  }
  .card--front { left: 200px; width: 369px; }
  .card--back  { left: 599px; width: 364px; }

  .front-artwork {
    position: absolute; left: 0; top: 0; width: 100%; height: 468px;
    background: linear-gradient(100deg, var(--orange) 0%, var(--orange) 52%, var(--blue) 56%, var(--blue) 100%);
  }
  .tagline {
    position: absolute; left: 0; right: 0; top: 492px;
    font-family: "Bebas Neue", sans-serif;
    font-size: 27px; line-height: 34px;
    color: var(--tagline-ink);
    text-align: center;
    letter-spacing: 0.2px;
  }

  .brand {
    position: absolute; left: 0; right: 0; top: 138px;
    display: flex; align-items: center; justify-content: center; gap: 8px;
  }
  .brand-dot { width: 12px; height: 12px; border-radius: 50%; background: var(--orange); }
  .brand-name { font-weight: 500; font-size: 24px; color: var(--orange); letter-spacing: 0.2px; }

  .person { position: absolute; left: 0; right: 0; top: 326px; text-align: center; }
  .person-name { font-weight: 600; font-size: 30px; line-height: 40px; }
  .person-name .first { color: var(--orange); }
  .person-name .last { color: var(--blue); }
  .person-role { font-size: 16px; line-height: 20px; color: var(--ink); }

  .icon-row {
    position: absolute; left: 0; right: 0; top: 395px;
    display: flex; align-items: center; justify-content: center; gap: 4px;
  }
  .icon-row .rule { width: 52px; height: 1px; background: var(--rule); margin: 0 4px; }
  .icon { width: 25px; height: 25px; border-radius: 3px; background: var(--orange); display: flex; align-items: center; justify-content: center; }
  .icon svg { width: 15px; height: 15px; }

  .contact { position: absolute; left: 0; right: 0; top: 426px; text-align: center; font-size: 16px; line-height: 21px; color: var(--ink); }
  .divider { position: absolute; left: 88px; width: 194px; top: 507px; height: 1px; background: var(--rule); }
  .address { position: absolute; left: 0; right: 0; top: 518px; text-align: center; font-size: 16px; line-height: 20px; color: var(--ink); }
</style>
</head>
<body>
  <section class="card card--front">
    <div class="front-artwork" role="img" aria-label="Illustration of a white bare tree on a split orange and blue background"></div>
    <p class="tagline">Wooden tables and furniture of<br>the highest quality</p>
  </section>

  <section class="card card--back">
    <div class="brand">
      <span class="brand-dot"></span>
      <span class="brand-name">Harborline Benches</span>
    </div>

    <div class="person">
      <p class="person-name"><span class="first">Daniel</span> <span class="last">Mercer</span></p>
      <p class="person-role">Managing Director</p>
    </div>

    <div class="icon-row">
      <span class="rule"></span>
      <span class="icon" aria-label="Phone">
        <svg viewBox="0 0 16 16"><path d="M2 6c0-2 2-3 6-3s6 1 6 3v1h-3V5.5H5V7H2z" fill="#fff"/><rect x="3" y="8" width="10" height="6" rx="1" fill="#fff"/></svg>
      </span>
      <span class="icon" aria-label="Email">
        <svg viewBox="0 0 16 16"><rect x="1.5" y="3.5" width="13" height="9" fill="none" stroke="#fff" stroke-width="1.3"/><path d="M1.5 3.5 8 9l6.5-5.5M1.5 12.5 6.5 8M14.5 12.5 9.5 8" fill="none" stroke="#fff" stroke-width="1.1"/></svg>
      </span>
      <span class="icon" aria-label="Website">
        <svg viewBox="0 0 16 16"><circle cx="8" cy="8" r="6.5" fill="#fff"/><path d="M4 5c2 0 2 2 4 2s1 3-1 3-1 2-2 3M10 3c0 2 2 2 3 3" fill="none" stroke="#ed7326" stroke-width="1.3"/></svg>
      </span>
      <span class="rule"></span>
    </div>

    <div class="contact">
      <p>044-555 018 273</p>
      <p>hello@harborline.com</p>
      <p>www.harborline.com</p>
    </div>

    <div class="divider"></div>

    <div class="address">
      <p>18, Quay Timber Road</p>
      <p>45210, Portmere</p>
    </div>
  </section>
</body>
</html>
```